Lurvik.no is a new website about pedagogical entrepreneurship. It's main target group is teachers. The Nordic Bureau for Digital Schooling and the National Office for Learning and Classrooms are leading the project.

The web page is meant to show examples of how different methods of entrepreneurship can be used pedagogical in a learning environment. The page will also support the user with examples of different teaching programs and other examples of best practice.

Pedagogical entrepreneurship is not about business and men in suits. It's a method for learning. The focus in the design should be on school, education and new ways of learning.

The final product should be motivating and engaging, but at the same time governmental and serious. We are not looking for something "flashy" and corporate-looking, but a moderate, task-focused and clean design that state quality.

We need designs for three pages:
1 - frontpage
2 - subpage ("Metoder og undervisningsopplegg")
3 - subpage ("Små-TOPP i Vassbygd")

The interaction design for these three pages will be uploaded as an attachment.

We would like you to find inspiration in the following websites:
- www.skapekraft.no
- www.giellu.no
- www.brightfernlab.com
- www.zyx.no
(more will be added)

Please use the attached logo, and feel free to use this as an inspiration for the rest of the design.

Target Market(s)

Teachers

Industry/Entity Type

Education

Requirements
Must have
• * Header with: Logo. Main navigation. Utility navigation. Search box.
* Footer
Should not have
• Images of men in suits.
Very strong graphical elements that stands out too much (we want it clean).

```html
<!DOCTYPE html>
<html lang="en">
<head>
<meta charset="utf-8">
<title>Lurvik.no – Pedagogical entrepreneurship</title>
<link rel="stylesheet" href="https://fonts.googleapis.com/css2?family=Source+Sans+3:wght@400;600;700&family=Noto+Serif:ital,wght@1,400;1,700&display=swap">
<style>
:root{
  --header-navy:#0b1e35;
  --intro-blue:#0a88d4;
  --hero-deep:#1a86cf;
  --hero-light:#5cc1ea;
  --page-bg:#f5f4f2;
  --brand-blue:#1479c4;
  --link-blue:#1f6fb7;
  --text:#333;
  --footer-navy:#213464;
  --footer-link:#dfe6f3;
  --accent-yellow:#f6c51a;
  --bullet:#6ab2e0;
  --sans:"Source Sans 3", "Trebuchet MS", sans-serif;
  --serif:"Noto Serif", Georgia, serif;
}
*{box-sizing:border-box;margin:0;padding:0}
html,body{width:885px;height:1200px;overflow:hidden}
body{position:relative;background:var(--page-bg);font-family:var(--sans);color:var(--text)}
.abs{position:absolute}
ul{list-style:none}
h2,h3,h4{font-weight:400}

/* header */
.site-header{left:0;top:0;width:885px;height:83px;background:var(--header-navy)}
.brand{left:105px;top:12px;display:flex;align-items:center;gap:14px}
.brand-mark{width:48px;height:48px;border-radius:50%;background:#3a8fd6}
.brand-name{font-size:40px;font-weight:700;color:#3a9be0;line-height:1}
.brand-tagline{left:175px;top:56px;font-size:9px;color:#c9d8ea}
.search{left:607px;top:16px;display:flex}
.search-field{width:160px;height:16px;background:#fff;border:1px solid #aac;font-size:9px;padding:1px 4px;color:#555}
.search-button{width:15px;height:16px;background:#1b5fb0}
.main-nav{right:103px;top:52px;display:flex;gap:21px}
.main-nav a{color:#fff;font-size:12px;font-weight:700;text-decoration:none;letter-spacing:.1px}

/* intro */
.intro{left:0;top:83px;width:885px;height:96px;background:var(--intro-blue)}
.intro-text{left:123px;top:97px;width:585px;font-family:var(--serif);font-style:italic;font-size:15.5px;line-height:20px;color:#d9efff}
.intro-text strong{color:#fff}
.intro-more{right:120px;top:140px;font-family:var(--serif);font-style:italic;font-size:15px;color:#fff}

/* hero */
.hero{left:0;top:179px;width:885px;height:277px;background:radial-gradient(ellipse at 50% 20%,var(--hero-light),var(--hero-deep) 75%)}
.hero-col{top:203px;width:230px;text-align:center;color:#fff}
.hero-kicker{font-size:14px;margin-bottom:4px}
.hero-title{font-size:24px;line-height:25px;font-weight:400}
.hero-board{top:293px;height:208px;width:220px;border-radius:4px;background:linear-gradient(#fafafa 0,#eef3f7 62%,#7cc2ea 62%,#6bbbe6 100%)}

/* meter */
.meter{left:104px;top:519px;width:205px;height:256px;border-radius:4px;background:linear-gradient(#fdfdfe,#dfe8f1);box-shadow:0 1px 3px rgba(0,0,0,.2)}
.meter-head{left:104px;top:519px;width:205px;height:51px;background:linear-gradient(#2a8ad6,#0f62b0);border-radius:4px 4px 0 0;color:#fff;font-size:17px;line-height:18px;padding:8px 13px}
.meter-dial{left:134px;top:580px;width:152px;height:152px;border-radius:50%;background:radial-gradient(circle,#2a2d33 55%,#c9ced3 70%,#f0f2f4 100%)}
.meter-button{left:118px;top:738px;width:178px;height:35px;background:linear-gradient(#ffd84a,#f2b20c);border-radius:3px;color:#113a7a;font-weight:700;font-size:15px;text-align:center;line-height:35px}

/* get started */
.started-title{left:341px;top:531px;font-size:22px;color:var(--brand-blue)}
.list-block{top:573px;width:192px}
.list-heading{font-size:11px;font-weight:700;color:var(--link-blue);padding-bottom:7px;border-bottom:1px dotted #bbb}
.list-block ul{margin-top:8px}
.list-block li{font-size:9px;height:17.2px;line-height:17px;padding-left:15px;position:relative}
.list-block li::before{content:"";position:absolute;left:0;top:4px;width:9px;height:9px;border-radius:50%;background:var(--bullet)}
.see-more{font-size:9px;color:var(--link-blue);margin-top:5px}

/* inspiration */
.inspiration{left:104px;top:799px;width:677px;height:209px;border-radius:4px;background:linear-gradient(#fff 40%,#e6edf3);box-shadow:0 1px 3px rgba(0,0,0,.2)}
.inspiration-title{left:125px;top:812px;font-size:20px;color:var(--brand-blue)}
.inspo-item{top:858px;width:143px}
.inspo-caption{font-size:11.5px;line-height:14px;color:#444;height:41px}
.inspo-photo{height:95px}
.arrow{top:942px}

/* footer */
.site-footer{left:0;top:1022px;width:885px;height:178px;background:var(--footer-navy)}
.footer-mark{left:105px;top:1046px;width:84px;height:84px;border-radius:50%;background:#3b87cf}
.footer-name{left:105px;top:1136px;font-size:13px;font-weight:700;color:#fff}
.footer-col{top:1041px}
.footer-col h4{font-size:11.5px;font-weight:700;color:#fff;margin-bottom:6px}
.footer-col li{font-size:9px;color:var(--footer-link);line-height:16px}
.footer-col .more{color:var(--accent-yellow)}
.copyright{left:105px;top:1175px;font-size:9.5px;color:#fff}
.share{right:112px;top:1176px;display:flex;align-items:center;gap:5px;font-size:11.5px;color:#fff}
.share-chip{padding:1px 4px;background:#3c5a98;font-size:9px}
.share-chip.chirper{background:#4fb6e6}
</style>
</head>
<body>

<header class="site-header abs"></header>
<div class="brand abs"><span class="brand-mark"></span><span class="brand-name">Lurvik</span></div>
<div class="brand-tagline abs">Entreprenørielle metoder i undervisningen</div>
<form class="search abs"><div class="search-field">Search</div><div class="search-button"><svg width="15" height="16" viewBox="0 0 15 16"><circle cx="6.5" cy="7" r="3" fill="none" stroke="#fff" stroke-width="1.5"/><line x1="8.7" y1="9.3" x2="11.5" y2="12" stroke="#fff" stroke-width="1.6"/></svg></div></form>
<nav class="main-nav abs"><a href="#">BEST PRACTICE SCHOOLS</a><a href="#">LURVIKOMETER</a><a href="#">ABOUT LURVIK.NO</a></nav>

<section class="intro abs"></section>
<p class="intro-text abs"><strong>Pedagogical entrepreneurship works.</strong> Lorem ipsum dolor sit amet, consectetur adipisicing elit, sed do eiusmod tempor incididunt ut labore et dolore magna aliqua.</p>
<a class="intro-more abs">Learn more ›</a>

<section class="hero abs"></section>
<div class="hero-col abs" style="left:90px"><p class="hero-kicker">Learn about what, why and how!</p><h2 class="hero-title">What is pedagocical<br>entrepreneurship?</h2></div>
<div class="hero-col abs" style="left:325px"><p class="hero-kicker">Plan your lessons!</p><h2 class="hero-title">Methods and<br>teaching plans</h2></div>
<div class="hero-col abs" style="left:563px;top:206px"><p class="hero-kicker">Be inspired!</p><h2 class="hero-title">Good examples /<br>best practice</h2></div>
<div class="hero-board abs" role="img" aria-label="Cartoon presenter beside a projection screen showing a solution checklist" style="left:98px"></div>
<div class="hero-board abs" role="img" aria-label="Cartoon presenter beside a screen with a rising think, idea, try, do chart" style="left:334px"></div>
<div class="hero-board abs" role="img" aria-label="Cartoon presenter beside a screen with three tick boxes" style="left:572px"></div>

<div class="meter abs"></div>
<div class="meter-head abs">Are you working entrepreneurship-like?</div>
<div class="meter-dial abs" role="img" aria-label="Speedometer gauge illustration"></div>
<div class="meter-button abs">Try the lurvikometer!</div>

<h2 class="started-title abs">Get started!</h2>
<div class="list-block abs" style="left:343px">
  <h3 class="list-heading">Methods</h3>
  <ul><li>Cafe-pedagogikk</li><li>Elevbedrift</li><li>Grundercamp</li><li>Story line</li><li>REAL</li><li>Grundercamp</li><li>Story line</li><li>REAL</li></ul>
  <p class="see-more">See more...</p>
</div>
<div class="list-block abs" style="left:562px">
  <h3 class="list-heading">Teaching plans</h3>
  <ul><li>Teaching plans title</li><li>Teaching plans title</li><li>Teaching plans title</li><li>Teaching plans title</li><li>Teaching plans title</li><li>Teaching plans title</li><li>Teaching plans title</li><li>Teaching plans title</li></ul>
  <p class="see-more">See more...</p>
</div>

<section class="inspiration abs"></section>
<h2 class="inspiration-title abs">Inspiration</h2>
<svg class="arrow abs" style="left:109px" width="8" height="10"><path d="M7 0 L0 5 L7 10Z" fill="#777"/></svg>
<svg class="arrow abs" style="left:768px" width="8" height="10"><path d="M0 0 L7 5 L0 10Z" fill="#777"/></svg>
<div class="inspo-item abs" style="left:125px"><p class="inspo-caption">Lorem ipsum dolor<br>sed do eiusmod</p><div class="inspo-photo" role="img" aria-label="Photo of students working together around a table" style="background:linear-gradient(135deg,#b4553a,#d9b9a3 55%,#8a4a34)"></div></div>
<div class="inspo-item abs" style="left:290px;top:861px"><p class="inspo-caption">Lorem ipsum dolor<br>sed do eiusmod</p><div class="inspo-photo" role="img" aria-label="Photo of adults seated in a classroom seminar" style="background:linear-gradient(135deg,#d8dde3,#8c93a3 55%,#5a6a8a)"></div></div>
<div class="inspo-item abs" style="left:454px;top:861px"><p class="inspo-caption">Lorem ipsum dolor<br>sed do eiusmod</p><div class="inspo-photo" role="img" aria-label="Photo of a smiling teacher in front of a class" style="background:linear-gradient(135deg,#c9d6e4,#3d6fb8 55%,#a33c3c)"></div></div>
<div class="inspo-item abs" style="left:618px;top:861px"><p class="inspo-caption">Lorem ipsum dolor<br>sed do eiusmod</p><div class="inspo-photo" role="img" aria-label="Photo of a cheering group of people" style="background:linear-gradient(180deg,#f1f3f5,#c8c2bc 55%,#3e3e45)"></div></div>

<footer class="site-footer abs"></footer>
<div class="footer-mark abs"></div>
<div class="footer-name abs">Lurvik.no</div>
<div class="footer-col abs" style="left:231px"><h4>Pedagogical entrepreneurship</h4><ul><li>What is pedagogical entrepreneurship?</li><li>Science</li><li>Best practice schools</li><li>Lurvikometer</li><li>About lurvik.no</li></ul></div>
<div class="footer-col abs" style="left:434px"><h4>Methoda</h4><ul><li>Storyline</li><li>REAL</li><li>Cafe-pedagogikk</li><li class="more">See more...</li></ul></div>
<div class="footer-col abs" style="left:551px"><h4>Teaching plans</h4><ul><li>Lorem ipsum dolor</li><li>sed do eiusmod</li><li>Lorem ipsum dolor</li><li>sed do eiusmod</li><li class="more">See more...</li></ul></div>
<div class="footer-col abs" style="left:680px"><h4>Gode eksemplert</h4><ul><li>Lorem ipsum dolor</li><li>sed do eiusmod</li><li>Lorem ipsum dolor</li><li>sed do eiusmod</li><li class="more">See more...</li></ul></div>
<p class="copyright abs">© 2011 Pedagogical entrepreneurship.</p>
<div class="share abs">Share this! <span class="share-chip">Friendbook</span><span class="share-chip chirper">Chirper</span></div>

</body>
</html>
```